KTB PR Agency Stationery & Templates

I've started a public relations consulting firm and need the following digital design elements conveying a consistent brand image:
1. A logo that graphically reinforces the firm's name, which is Harbor Lantern Partners. A copy of the current logo file is attached for your review. This graphic was adapted the firm's web site design so it may require adjustment or modification but I don't believe we need to venture far from this design.
2. A business card design that will express quality when printed on high quality card stock.
3. Letterhead stationery and 2nd page in a digital file that possesses a quality appearance when output in an inkjet printer.
4. A news release template and 2nd page in a digital file that possesses a quality appearance when output in an inkjet printer.
5. An envelope design (4.125" X 9.5" business envelope) in a digital file that possesses a quality appearance when output in an inkjet printer.
6. A banner graphic consistent with the logo that can be used for the firm's Twitter, FaceBook and LinkedIn pages.
6. PowerPoint cover slide and slide templates
Thank you in advance.
Dale Morrow
Reason: Realized that initial timeframe was too short given the proposed project.
Reason: My schedule has been and will remain hectic so I'm extending the deadline by 5 days. A final decision will be made NLT 22 August.
Target Market(s)
Chief Executive Officers of public & private corporations ranging from $50 million US to $10 billion US in annual revenues.
Industry/Entity Type
Business
Look and feel
Each slider illustrates characteristics of the customer's brand and the style your logo design should communicate.

```html
<!DOCTYPE html>
<html lang="en">
<head>
<meta charset="utf-8">
<title>Harbor Lantern Partners – Stationery</title>
<link rel="stylesheet" href="https://fonts.googleapis.com/css2?family=Fira+Sans:wght@400;500&display=swap">
<style>
  :root {
    --page: #ffffff;
    --brand-blue: #2f6f8e;
    --brand-green: #3a9a46;
    --ink: #1a1a1a;
    --rule: #2b2b6b;
    --purple: #4b2a86;
    --envelope-top: #d9d7d7;
    --envelope-bottom: #141414;
    --window: #fbfbfa;
  }
  * { margin: 0; padding: 0; box-sizing: border-box; }
  html, body { width: 1200px; height: 849px; overflow: hidden; background: var(--page); }
  body { position: relative; font-family: "Fira Sans", Arial, sans-serif; }

  .wordmark { position: absolute; display: flex; align-items: center; gap: 10px; color: var(--brand-blue); font-weight: 500; line-height: 1; }
  .wordmark__name { display: flex; flex-direction: column; }
  .wordmark__mark { border: 3px solid var(--brand-green); border-radius: 50%; flex: none; }

  .wordmark--primary { left: 83px; top: 72px; font-size: 36px; }
  .wordmark--primary .wordmark__mark { width: 38px; height: 38px; }

  .envelope { position: absolute; left: 49px; top: 409px; width: 533px; height: 401px; border: 1px solid #000; background: var(--envelope-bottom); overflow: hidden; }
  .envelope__upper { position: absolute; left: 0; top: 0; right: 0; height: 206px; background: var(--envelope-top); }
  .envelope__band { position: absolute; left: 0; right: 0; top: 206px; height: 4px; background: var(--purple); }
  .envelope .wordmark { left: 186px; top: 36px; font-size: 27px; }
  .envelope .wordmark__mark { width: 30px; height: 30px; border-width: 2px; }
  .envelope__window { position: absolute; left: 124px; top: 143px; width: 291px; height: 138px; background: var(--window); border: 2px solid #000; border-radius: 2px; }

  .letterhead { position: absolute; left: 632px; top: 77px; width: 534px; height: 401px; border: 1px solid #222; background: #fff; }
  .letterhead__mark { position: absolute; left: 8px; top: 10px; width: 16px; height: 16px; border: 1.5px solid var(--brand-green); border-radius: 50%; }
  .letterhead__top-rule { position: absolute; left: 40px; right: 0; top: 17px; height: 1px; background: var(--rule); }
  .letterhead__footer { position: absolute; left: 0; right: 0; top: 371px; display: flex; align-items: center; gap: 6px; }
  .letterhead__footer-rule { height: 1px; background: var(--rule); }
  .letterhead__footer-rule--left { flex: 1; }
  .letterhead__footer-rule--right { width: 76px; }
  .letterhead__footer-name { font-size: 7px; font-weight: 500; color: var(--brand-blue); letter-spacing: 0.2px; text-transform: uppercase; }
</style>
</head>
<body>
  <div class="wordmark wordmark--primary">
    <div class="wordmark__name"><span>Harbor Lantern</span><span>Partners</span></div>
    <span class="wordmark__mark"></span>
  </div>

  <section class="envelope" aria-label="Envelope">
    <div class="envelope__upper"></div>
    <div class="envelope__band"></div>
    <div class="wordmark">
      <div class="wordmark__name"><span>Harbor Lantern</span><span>Partners</span></div>
      <span class="wordmark__mark"></span>
    </div>
    <div class="envelope__window"></div>
  </section>

  <section class="letterhead" aria-label="Letterhead">
    <span class="letterhead__mark"></span>
    <div class="letterhead__top-rule"></div>
    <div class="letterhead__footer">
      <div class="letterhead__footer-rule letterhead__footer-rule--left"></div>
      <span class="letterhead__footer-name">Harbor Lantern</span>
      <div class="letterhead__footer-rule letterhead__footer-rule--right"></div>
    </div>
  </section>
</body>
</html>
```